KRV Photography Business Card Design

I would like a business card designed in the shape of a camera.
Would like to see various camera designs. Would like to see what the card looks like in different colors. Would like to see which logo looks better on the various camera designs so please show me some with the white logo and some with the black logo. If you need a different file formats please let me know.
Project Deadline Extended Reason: My grandfather passed away and dealing with funeral plans so need to extend deadline. Added Tuesday, March 1, 2016
Project Deadline Extended
Reason: I just got back from out of town. My grandfather's passing was the primary focus for me these past few weeks and the funeral is over so now I will concentrate on picking my business card design. I really appreciate each designer who has taken the time to submit a design. Your effort has not gone unnoticed. I look forward to seeing more amazing designs.
Business
Contact Information for Business Card
Dorine
555-418-2706
https://www.facebook.com/krvphotographyfreelance/
MonaDorine@krv-photography.example

```html
<!DOCTYPE html>
<html lang="en">
<head>
<meta charset="UTF-8">
<title>KRV Photography – Camera Business Cards</title>
<link href="https://fonts.googleapis.com/css2?family=Open+Sans:wght@400;600;700&display=swap" rel="stylesheet">
<style>
  :root {
    --backdrop: #bdbec0;
    --card-black: #000000;
    --accent-gold: #c98a2e;
    --logo-gold: #d6a63c;
    --text-white: #ffffff;
  }
  * { margin: 0; padding: 0; box-sizing: border-box; }
  html, body {
    width: 1200px; height: 927px; overflow: hidden;
    background: var(--backdrop);
    font-family: "Open Sans", sans-serif;
  }
  .canvas { position: relative; width: 1200px; height: 927px; }

  .camera-card {
    position: absolute; top: 266px;
    width: 536px; height: 395px;
  }
  .camera-card--gold { left: 48px; --ink: var(--accent-gold); }
  .camera-card--white { left: 616px; --ink: var(--text-white); }

  .camera-card__shape {
    position: absolute; inset: 0;
    filter: drop-shadow(6px 8px 7px rgba(0,0,0,0.35));
  }
  .camera-card__shape path, .camera-card__shape rect { fill: var(--card-black); }

  .holder-name {
    position: absolute; left: 23px; top: 40px;
    font-size: 25px; font-weight: 700; letter-spacing: 2.2px;
    color: var(--ink); line-height: 1;
  }
  .contact-list {
    position: absolute; left: 23px; top: 81px;
    list-style: none; color: var(--ink);
    font-size: 15px; font-weight: 600; letter-spacing: 0.9px; line-height: 19px;
  }
  .contact-list li { display: flex; align-items: center; }
  .contact-list svg { width: 12px; height: 12px; margin-right: 13px; flex: none; }
  .contact-list svg * { fill: none; stroke: var(--accent-gold); stroke-width: 1.4; }
  .camera-card--white .contact-list svg * { stroke: var(--text-white); }

  .brand {
    position: absolute; left: 300px; top: 283px; width: 220px;
    display: flex; flex-direction: column; align-items: center;
  }
  .brand__dot {
    width: 64px; height: 64px; border-radius: 50%;
    background: var(--logo-gold); margin-bottom: 14px;
  }
  .brand__name {
    font-size: 17px; font-weight: 400; letter-spacing: 0.6px;
    color: var(--logo-gold); white-space: nowrap;
  }
</style>
</head>
<body>
<main class="canvas">

  <section class="camera-card camera-card--gold">
    <svg class="camera-card__shape" viewBox="0 0 536 395" width="536" height="395" aria-hidden="true">
      <rect x="71" y="18" width="63" height="20" rx="5"/>
      <rect x="377" y="0" width="104" height="36" rx="10"/>
      <rect x="0" y="23" width="536" height="372" rx="23"/>
    </svg>
    <h2 class="holder-name">THEO MARLOW</h2>
    <ul class="contact-list">
      <li><svg viewBox="0 0 12 12"><path d="M3 1 L4.5 3.5 L3.5 4.8 Q4.8 7.5 7.2 8.6 L8.5 7.6 L11 9 L10 11 Q4 11 1 2 Z"/></svg>+330 5550-1472</li>
      <li><svg viewBox="0 0 12 12"><rect x="1" y="2.5" width="10" height="7"/><path d="M1 2.5 L6 6.5 L11 2.5"/></svg>theo@marlowmail.example</li>
    </ul>
    <div class="brand">
      <span class="brand__dot"></span>
      <span class="brand__name">KRV PHOTOGRAPHY</span>
    </div>
  </section>

  <section class="camera-card camera-card--white">
    <svg class="camera-card__shape" viewBox="0 0 536 395" width="536" height="395" aria-hidden="true">
      <rect x="71" y="18" width="63" height="20" rx="5"/>
      <rect x="377" y="0" width="104" height="36" rx="10"/>
      <rect x="0" y="23" width="536" height="372" rx="23"/>
    </svg>
    <h2 class="holder-name">THEO MARLOW</h2>
    <ul class="contact-list">
      <li><svg viewBox="0 0 12 12"><path d="M3 1 L4.5 3.5 L3.5 4.8 Q4.8 7.5 7.2 8.6 L8.5 7.6 L11 9 L10 11 Q4 11 1 2 Z"/></svg>+330 5550-1472</li>
      <li><svg viewBox="0 0 12 12"><rect x="1" y="2.5" width="10" height="7"/><path d="M1 2.5 L6 6.5 L11 2.5"/></svg>theo@marlowmail.example</li>
    </ul>
    <div class="brand">
      <span class="brand__dot"></span>
      <span class="brand__name">KRV PHOTOGRAPHY</span>
    </div>
  </section>

</main>
</body>
</html>
```